BLS Business Card 2018

Larkmere Chiropractic. We have two locations that we want to advertise on the same card. Brightvale OrthoCore campus address: 3815 Pellham Dr., Suite 240, Flowood, MS 39417. Madison address: 246 Willowmere Dr., Building D., Madison, MS 39284. website: www.drlarkmere-example.com. o:(601)555-0147 f:(601)555-0183

Target Market(s)

Health care decision makers: primary care doctors and mothers

Contact Information for Business Card

I have no idea; up for any suggestions and I'd do much better picking from examples versus describing what I'm looking for. We are in a very high end location and would like the cards to look really sharp.

Requirements
Must have
• My name, Martin R Belvane, D.C.

```html
<!DOCTYPE html>
<html lang="en">
<head>
<meta charset="utf-8">
<title>Larkmere Chiropractic – Business Card</title>
<link href="https://fonts.googleapis.com/css2?family=Cinzel:wght@400&family=Roboto+Condensed:wght@400;700&display=swap" rel="stylesheet">
<style>
  :root {
    --stage: #e8e5e0;
    --paper: #ffffff;
    --ink: #111111;
    --ink-soft: #555555;
    --band: #0c0c0c;
    --band-text: #f2f2f2;
  }
  * { margin: 0; padding: 0; box-sizing: border-box; }
  html, body { width: 1200px; height: 911px; overflow: hidden; background: var(--stage); }
  .canvas {
    width: 1200px; height: 911px;
    display: flex; flex-direction: column; align-items: center; justify-content: center; gap: 44px;
  }
  .card {
    width: 700px; height: 400px; background: var(--paper); position: relative;
    box-shadow: 0 6px 18px rgba(0,0,0,.18);
    font-family: "Roboto Condensed", Arial, sans-serif; color: var(--ink);
  }
  /* front */
  .card-front .brand {
    position: absolute; left: 120px; top: 70px;
    font-family: "Cinzel", serif; font-weight: 400; color: var(--ink);
    line-height: 1;
  }
  .brand-name { display: block; font-size: 52px; letter-spacing: 1px; }
  .brand-sub { display: block; font-size: 30px; letter-spacing: 2px; margin-top: 4px; }
  .holder-name {
    position: absolute; left: 40px; top: 200px;
    font-weight: 700; font-size: 20px; letter-spacing: .3px;
  }
  .phones {
    position: absolute; right: 36px; top: 32px; text-align: right;
    font-size: 13px; color: var(--ink-soft); line-height: 1.5;
  }
  .phone-line { display: flex; align-items: center; justify-content: flex-end; gap: 8px; }
  .phone-line svg { width: 12px; height: 12px; fill: var(--ink); }
  .band {
    position: absolute; left: 0; right: 0; bottom: 0; height: 150px;
    background: linear-gradient(180deg, #1a1a1a, var(--band));
    color: var(--band-text); font-size: 15px; line-height: 1.45;
    display: flex; justify-content: space-between; align-items: center; padding: 0 36px;
  }
  .address-right { text-align: right; }
  /* back */
  .card-back { display: flex; flex-direction: column; align-items: center; justify-content: center; }
  .back-mark {
    font-family: "Cinzel", serif; font-weight: 400; font-size: 30px; letter-spacing: 3px; color: var(--ink);
  }
  .website {
    position: absolute; bottom: 40px; left: 0; right: 0; text-align: center;
    font-size: 14px; letter-spacing: 6px; text-transform: uppercase; color: var(--ink-soft);
  }
</style>
</head>
<body>
<main class="canvas">
  <section class="card card-front">
    <div class="brand">
      <span class="brand-name">LARKMERE</span>
      <span class="brand-sub">CHIROPRACTIC</span>
    </div>
    <p class="holder-name">MARTIN R BELVANE, D.C.</p>
    <div class="phones">
      <div class="phone-line">(601)555-0147
        <svg viewBox="0 0 24 24" aria-hidden="true"><path d="M6.6 10.8a15 15 0 0 0 6.6 6.6l2.2-2.2c.3-.3.7-.4 1-.2 1.1.4 2.3.6 3.6.6.6 0 1 .4 1 1V20c0 .6-.4 1-1 1A17 17 0 0 1 3 4c0-.6.4-1 1-1h3.5c.6 0 1 .4 1 1 0 1.3.2 2.5.6 3.6.1.3 0 .7-.2 1z"/></svg>
      </div>
      <div class="phone-line">(601)555-0183
        <svg viewBox="0 0 24 24" aria-hidden="true"><path d="M6 2h10v6H6zM4 9h16a2 2 0 0 1 2 2v9H2v-9a2 2 0 0 1 2-2zm2 7v2h12v-2z"/></svg>
      </div>
    </div>
    <div class="band">
      <address class="address-left" style="font-style:normal">
        Brightvale OrthoCore campus :<br>
        3815 Pellham Dr., Suite 240<br>
        Flowood, MS 39417.
      </address>
      <address class="address-right" style="font-style:normal">
        Madison address:<br>
        246 Willowmere Dr., Building D.<br>
        Madison, MS 39284.
      </address>
    </div>
  </section>

  <section class="card card-back">
    <p class="back-mark">LARKMERE CHIROPRACTIC</p>
    <p class="website">www.drlarkmere-example.com</p>
  </section>
</main>
</body>
</html>
```